Trucking Company Website Design

We are working with a Trucking company in California. They provide trucking services for dirt, gravel, landscape bark, and landscape materials.

As you might imagine, there are no websites we could find for inspiration for trucking companies.

Thank you for taking the time to consider designing a website for us. We are web developers based in Stockton, CA, USA. Most of our projects go through the same process. Understanding this process may help you win a project with us. We custom-code all of our websites in-house. We don’t have any requirements as to what tools you use for your design, but we ask that you follow these guidelines.

IMAGES:
If you use any images or icons in the design, we ask that you have a link to the asset so we can purchase the image/icon. Most of the designs we submit do not have the customer’s images on them unless they have some great images. Be creative; show us the feeling you are trying to portray with your image choices. Use any royalty-free site you choose. We subscribe to Quillo and mainly use their images, but we can purchase images outside of Quillo. PLEASE NOTE: we will not submit designs to clients with watermarks on the images.

FONTS:
We ask that you identify the fonts you’re using in the design. This can be done in a message if you want. We typically use Varnex Fonts and Quillo Fonts.

CONTENT:
We're always open to different content and ideas. We often submit designs with stock images so the client can see our vision. We typically take pictures after the website launch to use their images with our vision. Lorem Ipsum is fine for paragraphs, but we ask that you make the Headers with correct English. We want to be able to show the vision and identify the sections of the website.

INSPIRATION:
We typically add a couple of links in the brief of websites we like to help you get started in your design.

REVISIONS:
We do not often ask for revisions of the designs unless we see something in the design that may not appeal to the client. If there are slight changes that we want to make, we do that in the development process.

FEEDBACK:
We rarely give feedback on designs during the design process. We are working on many website projects and do not have the time to provide feedback. We usually respond if your request is well thought out and asks specific questions, but a note asking “feedback, please” usually goes unanswered.

```html
<!DOCTYPE html>
<html lang="en">
<head>
<meta charset="utf-8">
<title>Ridgeway Materials — Trucking</title>
<link href="https://fonts.googleapis.com/css2?family=Audiowide&family=Roboto:wght@400;500;700&display=swap" rel="stylesheet">
<style>
:root{
  --blue:#1672ad;
  --blue-dark:#0f5f93;
  --red:#e3221f;
  --ink:#222;
  --muted:#777;
  --pale:#eef5fb;
  --white:#fff;
}
*{box-sizing:border-box;margin:0;padding:0}
html,body{width:1200px;height:4298px;overflow:hidden}
body{position:relative;font-family:"Roboto",Arial,sans-serif;color:var(--ink);background:var(--white)}
.abs{position:absolute}
.display{font-family:"Audiowide","Roboto",sans-serif;font-weight:400;letter-spacing:1px}
.photo{position:absolute}

/* header */
.topline{top:0;left:0;width:1200px;height:4px;background:var(--blue)}
.brand{display:flex;align-items:center;gap:14px}
.brand-name{font-family:"Roboto",sans-serif;font-weight:700;color:var(--blue);font-size:34px;line-height:0.95;letter-spacing:0.5px}
.brand-name small{display:block;font-size:22px;letter-spacing:2px}
.brand-mark{width:26px;height:26px;background:var(--red)}
.nav{top:66px;left:472px;display:flex;gap:34px;font-size:14px;font-weight:500;color:#444}
.nav .active{color:var(--blue)}
.btn{display:inline-flex;align-items:center;justify-content:center;background:var(--red);color:var(--white);font-weight:700;font-size:14px;border-radius:3px;text-decoration:none}

/* hero */
.hero{top:145px;left:0;width:1200px;height:620px;background:linear-gradient(180deg,#c98f5a 0%,#d99a5a 30%,#8a5a3f 60%,#4a3029 100%)}
.hero-title{left:111px;top:256px;font-size:44px;line-height:54px;color:#2a2a2a}
.hero-title span{color:var(--blue);display:block}
.hero-text{left:111px;top:380px;width:380px;font-size:19px;line-height:29px;color:#222}

/* about */
.about-band{top:656px;left:0;width:1200px;height:412px}
.label{font-size:15px;font-weight:700;letter-spacing:1.5px;text-transform:uppercase}
.about .label{color:var(--white)}
.frame{background:var(--white);padding:7px;box-shadow:0 4px 14px rgba(0,0,0,.2)}
.frame .fill{width:100%;height:100%}

/* section heading */
.sec-head{left:0;width:1200px;text-align:center}
.sec-head .label{color:var(--red);display:inline-flex;align-items:center;gap:12px;font-family:"Audiowide",sans-serif;font-weight:400;font-size:16px;letter-spacing:1px}
.sec-head .label::before,.sec-head .label::after{content:"";width:30px;height:2px;background:var(--red)}
.sec-head h2{color:var(--blue);font-size:44px;margin-top:4px}

.service-name{top:1939px;font-size:17px;font-weight:700;color:var(--white);text-transform:uppercase;transform:translateX(-50%);white-space:nowrap}
.arrow-btn{width:42px;height:42px;background:var(--white);display:flex;align-items:center;justify-content:center;box-shadow:0 2px 6px rgba(0,0,0,.2)}

/* why */
.why-list{left:672px;top:2305px;list-style:none;font-size:15px;color:#555}
.why-list li{display:flex;align-items:center;gap:20px;height:34.4px}

/* blog */
.card{background:var(--white);box-shadow:0 4px 16px rgba(0,0,0,.12);padding:6px}
.card .fill{height:203px}
.card .body{padding:16px 12px 0}
.card .date{font-size:13px;color:#666;display:flex;gap:8px;align-items:center}
.card h3{font-size:17px;font-weight:500;line-height:25px;margin-top:12px;text-transform:uppercase}
.card p{font-size:13px;color:var(--muted);line-height:25px;margin-top:6px}
.card a{display:block;margin-top:8px;font-size:13px;font-weight:700;color:var(--red)}

/* contact */
.contact{top:3395px;left:0;width:1200px;height:566px;background:var(--pale)}
.field{background:var(--white);font-size:14px;color:#555;padding:16px;border:1px solid #e3e9ef}

/* footer */
.footer{top:3974px;left:0;width:1200px;height:324px;background:var(--blue)}
.footer-line{top:3960px;left:0;width:1200px;height:5px;background:var(--blue)}
.fcol h4{font-size:15px;font-weight:700;color:var(--white);margin-bottom:20px}
.fcol ul{list-style:none;font-size:14px;color:var(--white)}
.fcol li{display:flex;gap:16px;align-items:flex-start;height:32px}
.bar{top:4247px;left:0;width:1200px;height:51px;background:var(--blue-dark);color:var(--white);font-size:11px;text-align:center;line-height:51px}
</style>
</head>
<body>

<div class="abs topline"></div>

<!-- header -->
<div class="abs brand" style="left:110px;top:44px">
  <div class="brand-name">RIDGEWAY<small>MATERIALS</small></div>
  <div class="brand-mark"></div>
</div>
<nav class="abs nav">
  <span class="active">HOME</span><span>ABOUT US</span><span>SERVICES</span><span>BLOG</span><span>CONTACT US</span>
</nav>
<a class="abs btn" style="left:955px;top:52px;width:133px;height:46px">GET A QUOTE</a>

<!-- hero -->
<div class="abs hero" role="img" aria-label="Semi truck with trailer on a desert highway at sunset"></div>
<h1 class="abs hero-title display"><span>RIDGEWAY</span>MATERIALS</h1>
<p class="abs hero-text">Lorem ipsum dolor sit amet, consectetur elit, sed do eiusmodea.</p>
<a class="abs btn" style="left:111px;top:467px;width:137px;height:45px;font-size:13px">GET STARTED</a>
<svg class="abs" style="left:110px;top:563px" width="48" height="160" viewBox="0 0 48 160">
  <rect x="9" y="9" width="30" height="30" transform="rotate(45 24 24)" fill="none" stroke="#fff" stroke-width="2"/>
  <path d="M18 21l6 6 6-6" fill="none" stroke="#fff" stroke-width="2"/>
  <line x1="24" y1="62" x2="24" y2="156" stroke="#fff" stroke-width="2"/>
</svg>

<!-- about band -->
<svg class="abs about-band" width="1200" height="412" viewBox="0 0 1200 412">
  <polygon points="0,0 1200,104 1200,412 0,412" fill="#1672ad"/>
</svg>
<div class="about">
  <div class="abs label" style="left:111px;top:814px;display:flex;align-items:center;gap:14px"><span style="width:30px;height:2px;background:#fff;display:inline-block"></span>ABOUT US</div>
  <h2 class="abs display" style="left:111px;top:843px;color:#fff;font-size:31px;line-height:39px">WELCOME TO<br>RIDGEWAY MATERIALS</h2>
  <p class="abs" style="left:601px;top:814px;width:490px;color:#fff;font-size:15px;line-height:27.5px">Lorem ipsum dolor sit amet, consectetur adipiscing elit, sed do eiusmod tempor incididunt ut labore et dolore magna aliqua. Ut enim ad minim veniam, quis nostrud exercitation ullamco laboris nisi ut aliquip ex ea commodo consequat. Duis aute irure dolor in reprehenderit in voluptate velit esse cillum dolore eu fugiat nulla pariatur.</p>
</div>
<div class="abs frame" style="left:111px;top:963px;width:396px;height:327px"><div class="fill" role="img" aria-label="Dump truck unloading gravel" style="background:linear-gradient(180deg,#9cc0e0,#c7d6e3 45%,#8b8478)"></div></div>
<div class="abs frame" style="left:565px;top:1026px;width:523px;height:329px"><div class="fill" role="img" aria-label="Highway through green hills at sunrise with trucks" style="background:linear-gradient(180deg,#c9a061,#6f7d4c 55%,#3f4d2b)"></div></div>

<!-- services -->
<div class="abs sec-head" style="top:1468px">
  <div class="label">SERVICES</div>
  <h2 class="display">OUR SERVICES</h2>
</div>
<svg class="abs" style="left:0;top:1581px" width="1200" height="411" viewBox="0 0 1200 411">
  <defs>
    <linearGradient id="g1" x1="0" y1="0" x2="0" y2="1"><stop offset="0" stop-color="#b9a28a"/><stop offset="1" stop-color="#6b4a33"/></linearGradient>
    <linearGradient id="g2" x1="0" y1="0" x2="0" y2="1"><stop offset="0" stop-color="#8fb6dc"/><stop offset="1" stop-color="#5a4634"/></linearGradient>
    <linearGradient id="g4" x1="0" y1="0" x2="0" y2="1"><stop offset="0" stop-color="#d99a52"/><stop offset="1" stop-color="#4b5a36"/></linearGradient>
  </defs>
  <polygon points="0,0 267,0 325,411 0,411" fill="url(#g1)" role="img" aria-label="Excavator loading dirt into a truck"/>
  <polygon points="272,0 576,0 628,411 334,411" fill="url(#g2)" role="img" aria-label="Dump truck unloading gravel"/>
  <polygon points="576,0 876,0 928,411 639,411" fill="#e0463f" role="img" aria-label="Log truck carrying landscape bark"/>
  <polygon points="881,0 1200,0 1200,411 943,411" fill="url(#g4)" role="img" aria-label="Trucks on highway at sunset"/>
</svg>
<div class="abs service-name" style="left:159px">DIRT</div>
<div class="abs service-name" style="left:466px">GRAVEL</div>
<div class="abs service-name" style="left:778px">LANDSCAPE BARK</div>
<div class="abs service-name" style="left:1068px">LANDSCAPE MATERIALS</div>
<div class="abs arrow-btn" style="left:0;top:1765px"><svg width="14" height="14" viewBox="0 0 14 14"><path d="M9 2L4 7l5 5" fill="none" stroke="#1672ad" stroke-width="2"/></svg></div>
<div class="abs arrow-btn" style="left:1158px;top:1765px"><svg width="14" height="14" viewBox="0 0 14 14"><path d="M5 2l5 5-5 5" fill="none" stroke="#1672ad" stroke-width="2"/></svg></div>

<!-- why choose -->
<div class="photo" role="img" aria-label="Semi trucks on a highway at sunrise" style="left:130px;top:2148px;width:343px;height:384px;background:linear-gradient(180deg,#8fb2d3,#cfc2a0 45%,#6b6a66)"></div>
<svg class="abs" style="left:205px;top:2542px" width="120" height="42" viewBox="0 0 120 42">
  <defs><pattern id="dots" width="10" height="10" patternUnits="userSpaceOnUse"><circle cx="2" cy="2" r="1.6" fill="#c4c4c4"/></pattern></defs>
  <rect width="120" height="42" fill="url(#dots)"/>
</svg>
<div class="photo" role="img" aria-label="Excavator loading a truck on a construction site" style="left:336px;top:2320px;width:274px;height:289px;border:6px solid #fff;background:linear-gradient(180deg,#9bc0e0,#c9ad6f 55%,#6e5a42)"></div>
<div class="abs label" style="left:672px;top:2179px;color:var(--red);display:flex;align-items:center;gap:14px;font-family:'Audiowide',sans-serif;font-weight:400;font-size:16px"><span style="width:30px;height:2px;background:var(--red);display:inline-block"></span>WHY CHOOSE US</div>
<h2 class="abs display" style="left:672px;top:2206px;color:var(--blue);font-size:30px;line-height:38px">WHY CHOOSE<br>RIDGEWAY MATERIALS</h2>
<ul class="abs why-list">
  <li><svg width="15" height="15" viewBox="0 0 16 16"><circle cx="8" cy="8" r="8" fill="#e3221f"/><path d="M6 4.5L9.5 8 6 11.5" fill="none" stroke="#fff" stroke-width="2"/></svg>Lorem ipsum dolor sit amet</li>
  <li><svg width="15" height="15" viewBox="0 0 16 16"><circle cx="8" cy="8" r="8" fill="#e3221f"/><path d="M6 4.5L9.5 8 6 11.5" fill="none" stroke="#fff" stroke-width="2"/></svg>Consectetur adipiscing elit, sed do</li>
  <li><svg width="15" height="15" viewBox="0 0 16 16"><circle cx="8" cy="8" r="8" fill="#e3221f"/><path d="M6 4.5L9.5 8 6 11.5" fill="none" stroke="#fff" stroke-width="2"/></svg>Sed ut perspiciatis unde omnis iste natus error sitea</li>
  <li><svg width="15" height="15" viewBox="0 0 16 16"><circle cx="8" cy="8" r="8" fill="#e3221f"/><path d="M6 4.5L9.5 8 6 11.5" fill="none" stroke="#fff" stroke-width="2"/></svg>Lorem ipsum dolor sit amet</li>
  <li><svg width="15" height="15" viewBox="0 0 16 16"><circle cx="8" cy="8" r="8" fill="#e3221f"/><path d="M6 4.5L9.5 8 6 11.5" fill="none" stroke="#fff" stroke-width="2"/></svg>Consectetur adipiscing elit, sed do</li>
  <li><svg width="15" height="15" viewBox="0 0 16 16"><circle cx="8" cy="8" r="8" fill="#e3221f"/><path d="M6 4.5L9.5 8 6 11.5" fill="none" stroke="#fff" stroke-width="2"/></svg>Sed ut perspiciatis unde omnis iste natus error sitea</li>
</ul>
<a class="abs btn" style="left:672px;top:2539px;width:132px;height:46px;font-size:13px">CONTACT US</a>

<!-- blog -->
<div class="abs sec-head" style="top:2725px">
  <div class="label">BLOG POST</div>
  <h2 class="display">LATEST BLOG</h2>
</div>
<div class="abs card" style="left:111px;top:2842px;width:309px;height:426px">
  <div class="fill" role="img" aria-label="Trucks on a highway beside green fields" style="background:linear-gradient(180deg,#9fc3e3,#7ea45a 55%,#8c8c8c)"></div>
  <div class="body"><div class="date"><svg width="13" height="13" viewBox="0 0 14 14"><rect x="1" y="2" width="12" height="11" fill="#1672ad"/><rect x="1" y="5" width="12" height="1" fill="#fff"/></svg>20 Jun 2023</div>
  <h3>Sed ut perspiciatis unde omnis iste nat</h3><p>Lorem ipsum dolor sit amet, consectetur adipiscing elit sed doea.</p><a>READ MORE</a></div>
</div>
<div class="abs card" style="left:446px;top:2842px;width:308px;height:426px">
  <div class="fill" role="img" aria-label="Dump truck unloading gravel" style="background:linear-gradient(180deg,#9cc0e0,#c7d6e3 45%,#8b8478)"></div>
  <div class="body"><div class="date"><svg width="13" height="13" viewBox="0 0 14 14"><rect x="1" y="2" width="12" height="11" fill="#1672ad"/><rect x="1" y="5" width="12" height="1" fill="#fff"/></svg>20 Jun 2023</div>
  <h3>Sed ut perspiciatis unde omnis iste nat</h3><p>Lorem ipsum dolor sit amet, consectetur adipiscing elit sed doea.</p><a>READ MORE</a></div>
</div>
<div class="abs card" style="left:780px;top:2842px;width:308px;height:426px">
  <div class="fill" role="img" aria-label="Aerial view of a bridge over a river among trees" style="background:linear-gradient(135deg,#3f6a2e,#6e8f4a 50%,#2e4a5c)"></div>
  <div class="body"><div class="date"><svg width="13" height="13" viewBox="0 0 14 14"><rect x="1" y="2" width="12" height="11" fill="#1672ad"/><rect x="1" y="5" width="12" height="1" fill="#fff"/></svg>20 Jun 2023</div>
  <h3>Sed ut perspiciatis unde omnis iste nat</h3><p>Lorem ipsum dolor sit amet, consectetur adipiscing elit sed doea.</p><a>READ MORE</a></div>
</div>

<!-- contact -->
<div class="abs contact"></div>
<div class="abs sec-head" style="top:3465px">
  <div class="label">CONTACT US</div>
  <h2 class="display">GET IN TOUCH</h2>
</div>
<div class="abs field" style="left:235px;top:3583px;width:359px;height:49px">First Name</div>
<div class="abs field" style="left:604px;top:3583px;width:361px;height:49px">Last Name</div>
<div class="abs field" style="left:235px;top:3647px;width:359px;height:48px">Phone</div>
<div class="abs field" style="left:604px;top:3647px;width:361px;height:48px">Email</div>
<div class="abs field" style="left:235px;top:3710px;width:730px;height:110px">Comment</div>
<a class="abs btn" style="left:509px;top:3835px;width:180px;height:52px;border-radius:0;font-size:15px">SEND MESSAGE</a>

<!-- footer -->
<div class="abs footer-line"></div>
<div class="abs footer"></div>
<div class="abs brand" style="left:111px;top:4106px">
  <div class="brand-name" style="color:#fff">RIDGEWAY<small>MATERIALS</small></div>
  <div class="brand-mark" style="background:#fff"></div>
</div>
<div class="abs fcol" style="left:472px;top:4030px">
  <h4>NAVIGATION</h4>
  <ul><li>›&nbsp; Home</li><li>›&nbsp; About Us</li><li>›&nbsp; Services</li><li>›&nbsp; Blog</li><li>›&nbsp; Contact Us</li></ul>
</div>
<div class="abs fcol" style="left:656px;top:4030px">
  <h4>QUICK LINKS</h4>
  <ul><li>›&nbsp; Privacy Policy</li><li>›&nbsp; Terms Of Use</li><li>›&nbsp; Help Center</li><li>›&nbsp; Disclaimer</li></ul>
</div>
<div class="abs fcol" style="left:865px;top:4030px">
  <h4>CONTACT US</h4>
  <ul>
    <li style="height:56px"><svg width="12" height="16" viewBox="0 0 12 16"><path d="M6 0a6 6 0 0 0-6 6c0 4 6 10 6 10s6-6 6-10a6 6 0 0 0-6-6z" fill="#9cc7e8"/><circle cx="6" cy="6" r="2" fill="#1672ad"/></svg><span>465, Lorum Ipsum Dolore,<br>California</span></li>
    <li style="height:38px"><svg width="14" height="14" viewBox="0 0 14 14"><path d="M3 1l2 3-1.5 1.5a8 8 0 0 0 5 5L10 9l3 2-1.5 2.5C6 13 1 8 .5 2.5z" fill="#9cc7e8"/></svg>+1 (888) 888 8888</li>
    <li><svg width="14" height="12" viewBox="0 0 14 12"><rect width="14" height="12" fill="#9cc7e8"/><path d="M0 0l7 6 7-6" fill="none" stroke="#1672ad" stroke-width="1.5"/></svg>info@ridgewaymaterials.com</li>
  </ul>
</div>
<div class="abs bar">© 2023 RIDGEWAY MATERIALS &nbsp;|&nbsp; All Rights Reserved</div>

</body>
</html>
```